Advertising company unique advertising platform

we need a logo design for a new company based in Australia Melbourne. We develop innovated advertising platform where consumer can use this platform to get regular discount, as business owner they can use this platform for free advertisement. Payment for this advertisement platform only payable every two weeks, when I generate revenue for their business

Industry/Entity Type

Advertising

Contact Information for Business Card

Dale Morven | Co-Founder |Managing Director
Suite 718 240 Wattlebrook Lane Melbourne Vic 3000

ABN 38 614 207 923
Tel: +61 0487 259 318 | Email: dale.morven@plivorantu.com

Font styles to use
Decorative
Script

Requirements
Must have
• Try few different design and some round corner business card
Should not have
• One round corner business card...try 4 different colour background not only black, make sure two side is designed. Be creative so imagine you are giving this to a client make sure has wow factor, if you can also try one design with engrave like all the logo, words look 3d feel
• The word Advertising Platform use attached file font

```html
<!DOCTYPE html>
<html lang="en">
<head>
<meta charset="utf-8">
<title>Plivorantu Business Card</title>
<link rel="stylesheet" href="https://fonts.googleapis.com/css2?family=Roboto:wght@400;500&family=Roboto+Condensed:wght@500;700&display=swap">
<style>
  :root {
    --backdrop: #5f4a3c;
    --card: #2b2a2a;
    --accent-red: #e0442a;
    --accent-teal: #1ee0a3;
    --text-light: #f4f4f4;
    --flame-deep: #e8452a;
    --flame-mid: #f37a2b;
    --flame-light: #f9b24a;
    --paper: #f2f2f2;
  }
  html, body {
    margin: 0;
    padding: 0;
    width: 1200px;
    height: 960px;
    overflow: hidden;
    background: var(--backdrop);
  }
  .stage {
    position: relative;
    width: 1200px;
    height: 960px;
  }
  .card {
    position: absolute;
    width: 598px;
    height: 343px;
    background: var(--card);
    border-radius: 22px;
    overflow: hidden;
    box-shadow: 0 4px 10px rgba(0,0,0,0.35);
    font-family: "Roboto", Arial, sans-serif;
    color: var(--text-light);
  }
  .card--front { left: 314px; top: 113px; }
  .card--back { left: 312px; top: 472px; }

  .identity {
    position: absolute;
    left: 75px;
    top: 40px;
    font-family: "Roboto Condensed", "Arial Narrow", sans-serif;
    text-transform: uppercase;
  }
  .identity__name {
    margin: 0;
    font-size: 21px;
    font-weight: 700;
    color: var(--accent-red);
    line-height: 24px;
  }
  .identity__role {
    margin: 0;
    font-size: 15.5px;
    font-weight: 500;
    color: var(--accent-teal);
    line-height: 19px;
    letter-spacing: 0.2px;
  }

  .details {
    position: absolute;
    left: 34px;
    top: 187px;
    font-size: 14.5px;
    line-height: 18px;
  }
  .details p { margin: 0; }
  .details__group { margin-bottom: 7px; }
  .contact-line {
    display: flex;
    align-items: center;
    gap: 8px;
    margin-left: 0;
    line-height: 19px;
  }
  .contact-line svg { width: 13px; height: 13px; flex: none; }

  .flame-panel {
    position: absolute;
    right: 0;
    top: 0;
    width: 236px;
    height: 343px;
  }
  .brand-seal {
    position: absolute;
    left: 411px;
    top: 156px;
    width: 160px;
    height: 160px;
    border-radius: 50%;
    background: var(--paper);
    display: flex;
    align-items: center;
    justify-content: center;
  }
  .brand-name {
    font-family: "Roboto", Arial, sans-serif;
    font-weight: 500;
    font-size: 21px;
    color: var(--accent-red);
  }

  .back-brand {
    position: absolute;
    left: 404px;
    top: 220px;
    width: 160px;
    text-align: center;
  }
  .back-brand .brand-name { font-size: 22px; }
  .website {
    position: absolute;
    left: 404px;
    top: 295px;
    font-size: 14.5px;
    letter-spacing: 0.2px;
  }
</style>
</head>
<body>
<main class="stage">
  <section class="card card--front">
    <header class="identity">
      <h1 class="identity__name">Dale Morven</h1>
      <p class="identity__role">Co-Founder</p>
      <p class="identity__role">Managing Director</p>
    </header>

    <div class="details">
      <div class="details__group">
        <p>Plivorantu</p>
        <p>ABN 38 614 207 923</p>
      </div>
      <div class="details__group">
        <p>Suite 718 240 Wattlebrook Lane</p>
        <p>Melbourne Vic 3000</p>
      </div>
      <p class="contact-line">
        <svg viewBox="0 0 24 24" aria-hidden="true"><path fill="#e0442a" d="M6.6 10.8a15.1 15.1 0 0 0 6.6 6.6l2.2-2.2a1 1 0 0 1 1-.25 11.4 11.4 0 0 0 3.6.57 1 1 0 0 1 1 1V20a1 1 0 0 1-1 1A17 17 0 0 1 3 4a1 1 0 0 1 1-1h3.5a1 1 0 0 1 1 1c0 1.25.2 2.45.57 3.6a1 1 0 0 1-.25 1z"/></svg>
        +61 0487 259 318
      </p>
      <p class="contact-line">
        <svg viewBox="0 0 24 24" aria-hidden="true"><rect x="2" y="5" width="20" height="14" rx="1.5" fill="#e0442a"/><path d="M3 6l9 7 9-7" fill="none" stroke="#2b2a2a" stroke-width="2"/></svg>
        dale.morven@plivorantu.com
      </p>
    </div>

    <svg class="flame-panel" viewBox="0 0 236 343" role="img" aria-label="Large flame illustration in orange tones around the brand seal">
      <defs>
        <linearGradient id="flameTone" x1="0" y1="1" x2="1" y2="0">
          <stop offset="0" stop-color="var(--flame-deep)"/>
          <stop offset="0.55" stop-color="var(--flame-mid)"/>
          <stop offset="1" stop-color="var(--flame-light)"/>
        </linearGradient>
      </defs>
      <rect x="0" y="0" width="236" height="343" fill="url(#flameTone)"/>
    </svg>

    <div class="brand-seal">
      <span class="brand-name">Plivorantu</span>
    </div>
  </section>

  <section class="card card--back">
    <div class="back-brand">
      <span class="brand-name">Plivorantu</span>
    </div>
    <p class="website">www.plivorantu.com</p>
  </section>
</main>
</body>
</html>
```